Business Card for Professional Photographer

I'm looking for an eye catching modern clean design that compliments my logo/ website fonts & colours.
I specialise in architecture, corporate & commercial photography so I'm marketing to professional clients rather than portrait / wedding clients.

I would prefer to not have a solid black design.

My logo brand guide is as follows :

Main front font. : Reislust
Main font colour : #fff
Slogan front font : Ubuntu Bold
Monogram front font : Venti Medium
Container colour : #fff

I need print ready files in pdf .png & .eps formats.

Included in the files below are some screen grabs as reference to font & colours etc.

```html
<!DOCTYPE html>
<html lang="en">
<head>
<meta charset="utf-8">
<title>Northlight Studio – Business Card</title>
<link href="https://fonts.googleapis.com/css2?family=Open+Sans:wght@300;400;600;700&display=swap" rel="stylesheet">
<style>
  :root {
    --backdrop: #e7e4df;
    --card: #262626;
    --card-edge: #1c1c1c;
    --gold: #c9a24a;
    --white: #f4f4f4;
    --muted: #d9d9d9;
  }
  * { margin: 0; padding: 0; box-sizing: border-box; }
  html, body {
    width: 1200px; height: 847px; overflow: hidden;
    background: var(--backdrop);
    font-family: "Open Sans", Arial, sans-serif;
  }
  .sheet {
    position: relative; width: 1200px; height: 847px;
    display: flex; align-items: center; justify-content: center; gap: 60px;
  }
  .card {
    position: relative; width: 520px; height: 297px;
    background: var(--card);
    border: 1px solid var(--card-edge);
    box-shadow: 0 6px 18px rgba(0,0,0,0.18);
  }
  /* Front */
  .card-front .brand {
    position: absolute; left: 70px; top: 118px;
    display: flex; align-items: center; gap: 16px;
  }
  .brand-mark {
    width: 14px; height: 14px; border-radius: 50%;
    background: var(--gold);
  }
  .brand-name {
    font-weight: 300; font-size: 27px; letter-spacing: 4px;
    color: var(--white); text-transform: uppercase; line-height: 1;
  }
  .brand-tagline {
    position: absolute; left: 100px; top: 158px;
    font-weight: 600; font-size: 9px; letter-spacing: 2.4px;
    color: var(--gold);
  }
  /* Back */
  .identity {
    position: absolute; right: 268px; top: 92px; text-align: right;
  }
  .person-name {
    font-weight: 700; font-size: 22px; color: var(--gold);
    letter-spacing: 0.2px; line-height: 1.2;
  }
  .person-role {
    font-weight: 400; font-size: 16px; color: var(--muted);
    margin-top: 4px;
  }
  .divider {
    position: absolute; left: 266px; top: 92px;
    width: 1.5px; height: 62px; background: var(--gold);
  }
  .contacts {
    position: absolute; left: 282px; top: 94px;
    list-style: none;
  }
  .contacts li {
    display: flex; align-items: center; gap: 5px;
    font-size: 15px; color: var(--white); line-height: 20px;
  }
  .contacts svg { width: 11px; height: 11px; flex: none; }
  .address {
    position: absolute; left: 60px; top: 206px;
    font-size: 17px; color: var(--white);
  }
</style>
</head>
<body>
<main class="sheet">
  <section class="card card-front" aria-label="Card front">
    <div class="brand">
      <span class="brand-mark"></span>
      <span class="brand-name">Northlight Studio</span>
    </div>
    <p class="brand-tagline">Architecture Corporate Commercial</p>
  </section>

  <section class="card card-back" aria-label="Card back">
    <div class="identity">
      <p class="person-name">DANIEL HARKER</p>
      <p class="person-role">Director</p>
    </div>
    <span class="divider"></span>
    <ul class="contacts">
      <li>
        <svg viewBox="0 0 12 12" aria-hidden="true"><path fill="var(--gold)" d="M2.3 1l2 2.2-1 1.2c.7 1.5 1.8 2.6 3.3 3.3l1.2-1 2.2 2-1.2 1.6C5.2 10.2 1.8 6.8 1 2.5z"/></svg>
        555 014 2290
      </li>
      <li>
        <svg viewBox="0 0 12 12" aria-hidden="true"><rect x="0.5" y="2.5" width="11" height="7" fill="var(--gold)"/><path d="M0.5 2.5l5.5 4 5.5-4" fill="none" stroke="var(--card)" stroke-width="1"/></svg>
        info@northlightstudio.com
      </li>
      <li>
        <svg viewBox="0 0 12 12" aria-hidden="true"><circle cx="6" cy="6" r="5.2" fill="var(--gold)"/><path d="M1 6h10M6 0.8c-2 2.8-2 7.6 0 10.4M6 0.8c2 2.8 2 7.6 0 10.4" fill="none" stroke="var(--card)" stroke-width="0.8"/></svg>
        www.northlightstudio.com
      </li>
    </ul>
    <p class="address">148 Linden Street, Brooklyn NY 11221</p>
  </section>
</main>
</body>
</html>
```